Family business needs stationery redesign with new logo

Family owned company, established in 1987 wanting a brand 'refresh'. We are an electrical, refrigeration and construction company based in the Barkly Region Northern Territory, Australia. We have a new logo we would like to use which is uploaded along with our current letterhead and email signature. We are also dropping the word 'contractors' so please do not include this on any designs. Please note also, the 'orange' color used in our logo and designs should be Northern Territory red ochre which is as follows:

RGB (Hex): #C75B12
PantoneĀ® 159 C
CMYK: 1 / 74 / 100 / 7

We are needing our stationery redesigned using our new logo. Please include letterheads, business cards, envelopes, and email signatures.

We currently use our business letterheads for quotations, invoices, letters, HR matters, and internal memos.

We also need a separate simplified letterhead for internal paperwork such as employee leave forms, meeting agendas, and meeting minutes etc.

Reason: Needing more submissions of full package designs. We are wanting all our stationery, including business cards, letterheads, email signatures, envelopes, etc to be cohesive. We also require ALL the information, as supplied on our template letterhead, to be included on the new letterhead designs. including electrical license no.etc Thank you, R&W

Reason: needing more time as work has got in the way of looking over designs. A lot of designs not meeting the brief/criteria.

Industry/Entity Type

Business

Colors
0355a3
f37122

Requirements
Must have
• The 'orange' color used in the designs should be Northern Territory red ochre which is as follows:
• RGB (Hex): #C75B12
• PantoneĀ® 159 C
• CMYK: 1 / 74 / 100 / 7
• ***MUST INCLUDE ALL INFORMATION THAT IS ON OUR CURRENT LETTERHEAD***
Should not have
• Please do not include the word 'contractors'

```html
<!DOCTYPE html>
<html lang="en">
<head>
<meta charset="utf-8">
<title>R&amp;W Stationery</title>
<link href="https://fonts.googleapis.com/css2?family=Saira:wght@400;700&family=Saira+Condensed:wght@400&display=swap" rel="stylesheet">
<style>
:root{
  --navy:#24398a;
  --orange:#ee5f1f;
  --paper:#ffffff;
  --bg:#f7c7a8;
  --ink:#555a66;
  --pattern:#eeeeef;
}
*{box-sizing:border-box;margin:0;padding:0}
html,body{width:1200px;height:900px;overflow:hidden}
body{background:var(--bg);position:relative;font-family:"Saira Condensed",sans-serif;color:var(--ink)}
.piece{position:absolute;background:var(--paper);overflow:hidden;box-shadow:0 2px 6px rgba(120,60,20,.18)}
.wordmark{display:flex;align-items:center;gap:6px;font-family:"Saira",sans-serif;font-weight:700;color:var(--navy);line-height:1}
.wordmark .dot{border-radius:50%;background:var(--orange);flex:none}
.tagline{font-family:"Saira Condensed",sans-serif;color:var(--ink);white-space:nowrap}
.tagline .sep{color:var(--orange);padding:0 .3em}
.accent{position:absolute;width:3px}
.accent.navy{background:var(--navy)}
.accent.orange{background:var(--orange)}
.base-band{position:absolute;left:0;right:0;bottom:0;height:4px;background:var(--orange)}
.base-band::after{content:"";position:absolute;right:0;top:0;bottom:0;width:30%;background:var(--navy);border-left:3px solid var(--paper)}
.footer{position:absolute;left:10px;right:10px;display:flex;justify-content:space-between;align-items:flex-end;font-size:6px;white-space:nowrap}
.footer .item{display:flex;flex-direction:column;align-items:center;gap:2px}
.footer svg{width:6px;height:6px}
/* business card front */
.card-front{left:60px;top:50px;width:340px;height:195px;border-radius:14px}
.card-front .wordmark{position:absolute;left:0;right:0;top:62px;justify-content:center;font-size:44px}
.card-front .wordmark .dot{width:14px;height:14px}
.card-front .tagline{position:absolute;left:0;right:0;top:122px;text-align:center;font-size:13px}
/* business card back */
.card-back{left:60px;top:275px;width:340px;height:195px;border-radius:14px}
.card-back .wordmark{position:absolute;left:34px;top:80px;font-size:32px}
.card-back .wordmark .dot{width:10px;height:10px}
.card-back .divider{position:absolute;left:168px;top:46px;width:1px;height:96px;background:#c8c8cc}
.contact{position:absolute;left:182px;top:46px;font-size:9.5px;line-height:1.45}
.contact .name{font-family:"Saira",sans-serif;font-weight:700;color:var(--orange);font-size:12px}
.contact .role{color:var(--ink);font-size:9px;margin-bottom:3px}
.contact li{list-style:none;display:flex;align-items:center;gap:5px}
.contact li::before{content:"";width:5px;height:5px;border-radius:50%;background:var(--orange)}
.card-back .base-band{height:6px}
/* letterhead */
.letterhead{left:470px;top:45px;width:330px;height:467px}
.letterhead .wordmark{position:absolute;left:0;right:0;top:24px;justify-content:center;font-size:34px}
.letterhead .wordmark .dot{width:10px;height:10px}
.letterhead .tagline{position:absolute;left:0;right:0;top:62px;text-align:center;font-size:7px}
.letterhead .footer{bottom:12px}
/* compliment slip */
.slip{left:60px;top:495px;width:340px;height:150px}
.slip .wordmark{position:absolute;left:20px;top:18px;font-size:24px}
.slip .wordmark .dot{width:8px;height:8px}
.slip .tagline{position:absolute;left:20px;top:46px;font-size:5.5px}
.slip .footer{bottom:11px;font-size:5px}
/* envelope */
.envelope{left:60px;top:672px;width:350px;height:190px}
.envelope .flap{position:absolute;left:0;right:0;top:0;height:48px;background:var(--orange);clip-path:polygon(0 0,100% 0,100% 40%,92% 100%,8% 100%,0 40%)}
.envelope .field{position:absolute;left:0;right:0;top:48px;bottom:0;background:var(--pattern)}
.envelope .wordmark{position:absolute;left:150px;top:140px;font-size:22px}
.envelope .wordmark .dot{width:7px;height:7px}
/* cover sheet */
.cover{left:830px;top:45px;width:330px;height:467px}
.cover .field{position:absolute;inset:0 0 5px 0;background:var(--pattern)}
.cover .wordmark{position:absolute;left:0;right:0;top:196px;justify-content:center;font-size:58px}
.cover .wordmark .dot{width:16px;height:16px}
.cover .tagline{position:absolute;left:0;right:0;top:262px;text-align:center;font-size:12px}
/* promo items */
.pen{position:absolute;left:500px;top:600px;width:420px;height:36px;border-radius:4px 18px 18px 4px;background:#f3f3f4;box-shadow:0 2px 6px rgba(120,60,20,.18)}
.pen .tip{position:absolute;left:-22px;top:12px;width:24px;height:12px;background:#dcdcde;clip-path:polygon(0 50%,100% 0,100% 100%)}
.pen .wordmark{position:absolute;left:150px;top:5px;font-size:22px}
.pen .wordmark.second{left:320px}
.pen .wordmark .dot{width:7px;height:7px}
.eraser{position:absolute;top:740px;width:140px;height:70px;background:var(--paper);border-radius:4px;box-shadow:0 2px 6px rgba(120,60,20,.18)}
.eraser .wordmark{position:absolute;left:0;right:0;top:20px;justify-content:center;font-size:26px}
.eraser .wordmark .dot{width:8px;height:8px}
.eraser.one{left:650px}
.eraser.two{left:840px}
</style>
</head>
<body>

<section class="piece card-front">
  <span class="accent orange" style="left:12px;top:100px;height:18px"></span>
  <span class="accent navy" style="left:12px;top:122px;height:18px"></span>
  <span class="accent orange" style="right:12px;top:26px;height:18px"></span>
  <span class="accent navy" style="right:12px;top:48px;height:18px"></span>
  <div class="wordmark">R&amp;W<span class="dot"></span></div>
  <p class="tagline">Electrical<span class="sep">|</span>Refrigeration<span class="sep">|</span>Building Services</p>
</section>

<section class="piece card-back">
  <div class="wordmark">R&amp;W<span class="dot"></span></div>
  <span class="divider"></span>
  <div class="contact">
    <p class="name">Dana Hollis</p>
    <p class="role">President</p>
    <ul>
      <li>PO Box 4410, Alder Creek NT 0870</li>
      <li>1-800-555-0142</li>
      <li>0400 111 222</li>
      <li>dana@rwservices.com.au</li>
      <li>www.rwservices.com.au</li>
    </ul>
  </div>
  <span class="base-band"></span>
</section>

<section class="piece slip">
  <span class="accent navy" style="left:6px;top:20px;height:14px"></span>
  <span class="accent orange" style="left:6px;top:38px;height:14px"></span>
  <span class="accent navy" style="right:6px;top:20px;height:14px"></span>
  <span class="accent orange" style="right:6px;top:38px;height:14px"></span>
  <div class="wordmark">R&amp;W<span class="dot"></span></div>
  <p class="tagline">Electrical<span class="sep">|</span>Refrigeration<span class="sep">|</span>Building Services</p>
  <div class="footer">
    <span class="item"><svg viewBox="0 0 10 10"><path d="M5 0a3.5 3.5 0 0 1 3.5 3.5C8.5 6 5 10 5 10S1.5 6 1.5 3.5A3.5 3.5 0 0 1 5 0z" fill="#24398a"/></svg>PO Box 4410 | 52 Ridge Rd, Alder Creek NT 0870</span>
    <span class="item"><svg viewBox="0 0 10 10"><circle cx="5" cy="5" r="5" fill="#24398a"/></svg>08 7100 0000</span>
    <span class="item"><svg viewBox="0 0 10 10"><circle cx="5" cy="5" r="5" fill="#24398a"/></svg>0400 111 222</span>
    <span class="item"><svg viewBox="0 0 10 10"><circle cx="5" cy="5" r="5" fill="#24398a"/></svg>08 7100 0001</span>
    <span class="item"><svg viewBox="0 0 10 10"><rect x="0" y="2" width="10" height="6" fill="#24398a"/></svg>hello@rwservices.com.au</span>
    <span class="item"><svg viewBox="0 0 10 10"><circle cx="5" cy="5" r="4" fill="none" stroke="#24398a" stroke-width="1.5"/></svg>www.rwservices.com.au</span>
  </div>
  <span class="base-band"></span>
</section>

<section class="piece envelope">
  <div class="flap" role="img" aria-label="Orange envelope flap with a tone-on-tone geometric pattern"></div>
  <div class="field" role="img" aria-label="Faint repeating brand-name pattern across the envelope"></div>
  <div class="wordmark">R&amp;W<span class="dot"></span></div>
</section>

<section class="piece letterhead">
  <span class="accent navy" style="left:6px;top:16px;height:26px"></span>
  <span class="accent orange" style="left:6px;top:46px;height:26px"></span>
  <span class="accent navy" style="right:6px;top:56px;height:26px"></span>
  <span class="accent orange" style="right:6px;top:86px;height:26px"></span>
  <div class="wordmark">R&amp;W<span class="dot"></span></div>
  <p class="tagline">Electrical<span class="sep">|</span>Refrigeration<span class="sep">|</span>Building Services</p>
  <div class="footer">
    <span class="item"><svg viewBox="0 0 10 10"><path d="M5 0a3.5 3.5 0 0 1 3.5 3.5C8.5 6 5 10 5 10S1.5 6 1.5 3.5A3.5 3.5 0 0 1 5 0z" fill="#24398a"/></svg>PO Box 4410 | 52 Ridge Rd, Alder Creek NT 0870</span>
    <span class="item"><svg viewBox="0 0 10 10"><circle cx="5" cy="5" r="5" fill="#24398a"/></svg>08 7100 0000</span>
    <span class="item"><svg viewBox="0 0 10 10"><circle cx="5" cy="5" r="5" fill="#24398a"/></svg>0400 111 222</span>
    <span class="item"><svg viewBox="0 0 10 10"><circle cx="5" cy="5" r="5" fill="#24398a"/></svg>08 7100 0001</span>
    <span class="item"><svg viewBox="0 0 10 10"><rect x="0" y="2" width="10" height="6" fill="#24398a"/></svg>hello@rwservices.com.au</span>
    <span class="item"><svg viewBox="0 0 10 10"><circle cx="5" cy="5" r="4" fill="none" stroke="#24398a" stroke-width="1.5"/></svg>www.rwservices.com.au</span>
  </div>
  <span class="base-band"></span>
</section>

<section class="piece cover">
  <div class="field" role="img" aria-label="Faint repeating brand-name pattern covering the sheet"></div>
  <div class="wordmark">R&amp;W<span class="dot"></span></div>
  <p class="tagline">Electrical<span class="sep">|</span>Refrigeration<span class="sep">|</span>Building Services</p>
  <span class="base-band"></span>
</section>

<div class="pen">
  <span class="tip"></span>
  <div class="wordmark">R&amp;W<span class="dot"></span></div>
  <div class="wordmark second">R&amp;W<span class="dot"></span></div>
</div>

<div class="eraser one"><div class="wordmark">R&amp;W<span class="dot"></span></div></div>
<div class="eraser two"><div class="wordmark">R&amp;W<span class="dot"></span></div></div>

</body>
</html>
```